Specialised investor in e-mobility and energy wants business card design

We need a business card design that fits our existing corporate design. <The look and feel must be 'sharp'/'clean', dynamic, communicate momentum, professionalism etc (as one would imagine from a firm in the financial sector). We like the idea of a reverse-side of the card that includes the logo, and the name and contact details on the other. We expect the deliverable to be whatever format might be required to be able to get cards printed directly by a service such as kelmo press. Our website is www.zub.capital

```html
<!DOCTYPE html>
<html lang="en">
<head>
<meta charset="utf-8">
<title>ZUB Capital – Business Card</title>
<link href="https://fonts.googleapis.com/css2?family=Bebas+Neue&family=Arimo:wght@400&display=swap" rel="stylesheet">
<style>
  :root {
    --stage: #e9e9e7;
    --card: #2a2a2a;
    --card-edge: #242424;
    --green: #6a9e3a;
    --white: #f4f4f2;
    --muted: #d8d8d6;
    --rule: #8a8a8a;
  }
  * { box-sizing: border-box; margin: 0; padding: 0; }
  html, body { width: 1200px; height: 963px; overflow: hidden; }
  body {
    background: var(--stage);
    display: flex;
    flex-direction: column;
    align-items: center;
    justify-content: center;
    gap: 60px;
    font-family: "Arimo", Arial, sans-serif;
  }
  .card {
    position: relative;
    width: 600px;
    height: 388px;
    border-radius: 22px;
    background: radial-gradient(ellipse at 45% 45%, #2f2f2f 0%, var(--card) 55%, var(--card-edge) 100%);
    border-bottom: 3px solid var(--green);
    overflow: hidden;
  }

  /* Front: name and contact details */
  .holder {
    position: absolute;
    left: 62px;
    top: 138px;
    font-family: "Bebas Neue", Impact, sans-serif;
    font-size: 50px;
    letter-spacing: 0.5px;
    line-height: 1;
  }
  .holder .given { color: var(--white); }
  .holder .family { color: var(--green); }
  .divider {
    position: absolute;
    left: 318px;
    top: 122px;
    width: 1px;
    height: 86px;
    background: var(--rule);
  }
  .contacts {
    position: absolute;
    left: 336px;
    top: 128px;
    list-style: none;
    color: var(--white);
    font-size: 15px;
  }
  .contacts li {
    display: flex;
    align-items: center;
    gap: 9px;
    height: 25px;
  }
  .contacts svg { width: 15px; height: 15px; fill: var(--green); flex: none; }
  .location {
    position: absolute;
    left: 86px;
    top: 272px;
    color: var(--muted);
    font-size: 15px;
  }
  .brand-small {
    position: absolute;
    right: 56px;
    bottom: 42px;
    display: flex;
    align-items: center;
    gap: 8px;
    color: var(--white);
    font-size: 20px;
  }
  .brand-small .dot { width: 10px; height: 10px; border-radius: 50%; background: var(--green); }

  /* Back: brand name */
  .back { display: flex; align-items: center; justify-content: center; }
  .brand-large {
    display: flex;
    align-items: center;
    gap: 16px;
    color: var(--white);
    font-size: 60px;
  }
  .brand-large .dot { width: 22px; height: 22px; border-radius: 50%; background: var(--green); }
</style>
</head>
<body>

  <section class="card front">
    <h1 class="holder"><span class="given">Martin</span> <span class="family">Kessler</span></h1>
    <div class="divider"></div>
    <ul class="contacts">
      <li>
        <svg viewBox="0 0 24 24" aria-hidden="true"><path d="M6.6 10.8a15.1 15.1 0 0 0 6.6 6.6l2.2-2.2a1 1 0 0 1 1-.25 11.4 11.4 0 0 0 3.6.57 1 1 0 0 1 1 1V20a1 1 0 0 1-1 1A17 17 0 0 1 3 4a1 1 0 0 1 1-1h3.5a1 1 0 0 1 1 1c0 1.25.2 2.45.57 3.57a1 1 0 0 1-.25 1z"/></svg>
        +41 79555 0148
      </li>
      <li>
        <svg viewBox="0 0 24 24" aria-hidden="true"><path d="M2 5h20v14H2z M3.5 6.5 12 13l8.5-6.5" fill="none" stroke="#6a9e3a" stroke-width="2"/></svg>
        martin@zub.capital
      </li>
      <li>
        <svg viewBox="0 0 24 24" aria-hidden="true"><circle cx="12" cy="12" r="9" fill="none" stroke="#6a9e3a" stroke-width="2"/><path d="M3 12h18M12 3c3 3 3 15 0 18M12 3c-3 3-3 15 0 18" fill="none" stroke="#6a9e3a" stroke-width="1.6"/></svg>
        www.zub.capital
      </li>
    </ul>
    <p class="location">Geneva, Switzerland</p>
    <div class="brand-small"><span class="dot"></span><span>ZUB Capital</span></div>
  </section>

  <section class="card back">
    <div class="brand-large"><span class="dot"></span><span>ZUB Capital</span></div>
  </section>

</body>
</html>
```